Print on top the name of the company: (Or Similar)
Lumora Cleaning & Disinfecting
Because your standards aren't standard.

We adhere to ALL QRV guidelines for both residential and commercial cleaning.

Infection Control is our ultimate goal.

Instructions:
Opening a residential and commercial cleaning and disinfecting company in south Florida.

Targeting high-end residential clients, commercial and healthcare facilities, specializing in Ambulatory Care Guidelines. With a concentration and expertise in targeting Covid 19 and other transmissible pathogens.

WELM trained.
Owned and operated by a licensed BSN Registered Nurse specially ​trained in Infection Control Prevention with over 25 years experience. Over two decades in Ambulatory Surgery Center Administration, Director of Nursing and Infection Control Prevention ad Consulting.

Looking to create a business flier that emphasizes Cleaning & Disinfection
along with the standard expectation for residential and Commercial cleaning services

Target Market(s)

Residential & Commercial

Font styles to use
Decorative

Requirements
Must have
• A checklist for cleaning services

```html
<!DOCTYPE html>
<html lang="en">
<head>
<meta charset="utf-8">
<title>Lumora Cleaning &amp; Disinfecting – Flyer</title>
<link rel="stylesheet" href="https://fonts.googleapis.com/css2?family=Kaushan+Script&family=Montserrat:wght@600;700&display=swap">
<style>
  :root {
    --page: #ffffff;
    --blue: #2b8ec6;
    --blue-deep: #1d7fb2;
    --green: #9dbb3a;
    --panel-grey: #e8e8e8;
    --body-grey: #ececec;
    --ink: #262626;
    --white: #ffffff;
  }
  * { margin: 0; padding: 0; box-sizing: border-box; }
  html, body {
    width: 1200px; height: 1200px; overflow: hidden;
    background: var(--page);
    font-family: "Montserrat", Arial, sans-serif;
  }
  .flyer {
    position: absolute; left: 110px; top: 253px;
    width: 981px; height: 694px;
    background: radial-gradient(ellipse at 50% 60%, #f7f7f7 0%, var(--body-grey) 70%);
    overflow: hidden;
  }
  .flyer-shapes { position: absolute; inset: 0; }
  .brand-title {
    position: absolute; left: 0; right: 0; top: 22px;
    text-align: center;
    font-family: "Kaushan Script", cursive;
    font-size: 66px; line-height: 1;
    color: var(--white);
    letter-spacing: 0.5px;
  }
  .service-card {
    position: absolute; top: 181px;
    height: 316px;
    border-radius: 19px;
    overflow: hidden;
    background: var(--panel-grey);
  }
  .service-card--commercial { left: 64px; width: 422px; }
  .service-card--residential { left: 511px; width: 418px; }
  .card-heading {
    height: 64px;
    background: var(--green);
    color: var(--white);
    font-weight: 700; font-size: 45px;
    letter-spacing: 1.5px;
    text-align: center; line-height: 66px;
  }
  .service-list {
    position: absolute; top: 80px;
    list-style: none;
  }
  .service-list li {
    position: relative;
    padding-left: 16px;
    font-weight: 700; font-size: 13.6px;
    line-height: 17px; margin-bottom: 5px;
    color: var(--ink);
  }
  .service-list li svg {
    position: absolute; left: 0; top: 3px;
    width: 10px; height: 10px;
  }
  .card-photo {
    position: absolute; left: 0; right: 0; bottom: 0; height: 122px;
  }
  .card-photo--office {
    background: linear-gradient(100deg, #3a3a3a 0%, #d9d6d0 30%, #eeeeee 45%, #9a9a9a 70%, #2e2e2e 100%);
  }
  .card-photo--home {
    background: linear-gradient(180deg, #e7e0d6 0%, #f1ede8 45%, #dcdad8 100%);
  }
  .call-pill {
    position: absolute; left: 53px; top: 539px;
    width: 876px; height: 56px;
    border-radius: 28px;
    background: var(--blue-deep);
    color: var(--white);
    font-weight: 700; font-size: 27px;
    text-align: center; line-height: 56px;
    letter-spacing: 0.3px;
  }
  .phone-line {
    position: absolute; left: 0; right: 0; top: 604px;
    display: flex; justify-content: center; align-items: center; gap: 20px;
    color: var(--ink);
    font-weight: 700; font-size: 80px; line-height: 80px;
    letter-spacing: 1px;
  }
  .phone-line svg { width: 66px; height: 66px; }
</style>
</head>
<body>
  <main class="flyer">
    <svg class="flyer-shapes" viewBox="0 0 981 694" width="981" height="694" aria-hidden="true">
      <path d="M0,126 Q490,176 981,116 L981,142 Q490,170 0,150 Z" fill="var(--green)"/>
      <path d="M0,0 H981 V118 Q490,170 0,124 Z" fill="var(--blue)"/>
      <path d="M0,124 Q490,170 981,118" fill="none" stroke="var(--white)" stroke-width="4"/>
      <path d="M0,580 Q490,548 981,580 V694 H0 Z" fill="var(--green)"/>
    </svg>

    <h1 class="brand-title">Lumora Cleaning &amp; Disinfecting</h1>

    <section class="service-card service-card--commercial">
      <h2 class="card-heading">COMMERCIAL</h2>
      <ul class="service-list" style="left:39px">
        <li><svg viewBox="0 0 10 10"><circle cx="5" cy="5" r="5" fill="var(--green)"/><path d="M2.6,5.2 L4.3,6.8 L7.4,3.4" fill="none" stroke="#fff" stroke-width="1.4"/></svg>Janitorial</li>
        <li><svg viewBox="0 0 10 10"><circle cx="5" cy="5" r="5" fill="var(--green)"/><path d="M2.6,5.2 L4.3,6.8 L7.4,3.4" fill="none" stroke="#fff" stroke-width="1.4"/></svg>Offices</li>
        <li><svg viewBox="0 0 10 10"><circle cx="5" cy="5" r="5" fill="var(--green)"/><path d="M2.6,5.2 L4.3,6.8 L7.4,3.4" fill="none" stroke="#fff" stroke-width="1.4"/></svg>Floor maintenance</li>
        <li><svg viewBox="0 0 10 10"><circle cx="5" cy="5" r="5" fill="var(--green)"/><path d="M2.6,5.2 L4.3,6.8 L7.4,3.4" fill="none" stroke="#fff" stroke-width="1.4"/></svg>Carpet cleaning</li>
      </ul>
      <ul class="service-list" style="left:217px">
        <li><svg viewBox="0 0 10 10"><circle cx="5" cy="5" r="5" fill="var(--green)"/><path d="M2.6,5.2 L4.3,6.8 L7.4,3.4" fill="none" stroke="#fff" stroke-width="1.4"/></svg>Move-ins</li>
        <li><svg viewBox="0 0 10 10"><circle cx="5" cy="5" r="5" fill="var(--green)"/><path d="M2.6,5.2 L4.3,6.8 L7.4,3.4" fill="none" stroke="#fff" stroke-width="1.4"/></svg>Move-outs.</li>
        <li><svg viewBox="0 0 10 10"><circle cx="5" cy="5" r="5" fill="var(--green)"/><path d="M2.6,5.2 L4.3,6.8 L7.4,3.4" fill="none" stroke="#fff" stroke-width="1.4"/></svg>Constructions clean-ups</li>
        <li><svg viewBox="0 0 10 10"><circle cx="5" cy="5" r="5" fill="var(--green)"/><path d="M2.6,5.2 L4.3,6.8 L7.4,3.4" fill="none" stroke="#fff" stroke-width="1.4"/></svg>Estate clean-outs</li>
      </ul>
      <div class="card-photo card-photo--office" role="img" aria-label="Photo of a worker in a protective suit disinfecting an office"></div>
    </section>

    <section class="service-card service-card--residential">
      <h2 class="card-heading">RESIDENTIAL</h2>
      <ul class="service-list" style="left:34px">
        <li><svg viewBox="0 0 10 10"><circle cx="5" cy="5" r="5" fill="var(--green)"/><path d="M2.6,5.2 L4.3,6.8 L7.4,3.4" fill="none" stroke="#fff" stroke-width="1.4"/></svg>House cleaning</li>
        <li><svg viewBox="0 0 10 10"><circle cx="5" cy="5" r="5" fill="var(--green)"/><path d="M2.6,5.2 L4.3,6.8 L7.4,3.4" fill="none" stroke="#fff" stroke-width="1.4"/></svg>Before and after party</li>
        <li><svg viewBox="0 0 10 10"><circle cx="5" cy="5" r="5" fill="var(--green)"/><path d="M2.6,5.2 L4.3,6.8 L7.4,3.4" fill="none" stroke="#fff" stroke-width="1.4"/></svg>Move-ins</li>
        <li><svg viewBox="0 0 10 10"><circle cx="5" cy="5" r="5" fill="var(--green)"/><path d="M2.6,5.2 L4.3,6.8 L7.4,3.4" fill="none" stroke="#fff" stroke-width="1.4"/></svg>Move-outs</li>
      </ul>
      <ul class="service-list" style="left:237px">
        <li><svg viewBox="0 0 10 10"><circle cx="5" cy="5" r="5" fill="var(--green)"/><path d="M2.6,5.2 L4.3,6.8 L7.4,3.4" fill="none" stroke="#fff" stroke-width="1.4"/></svg>Holiday cleaning</li>
        <li><svg viewBox="0 0 10 10"><circle cx="5" cy="5" r="5" fill="var(--green)"/><path d="M2.6,5.2 L4.3,6.8 L7.4,3.4" fill="none" stroke="#fff" stroke-width="1.4"/></svg>Seasonal cleaning</li>
        <li><svg viewBox="0 0 10 10"><circle cx="5" cy="5" r="5" fill="var(--green)"/><path d="M2.6,5.2 L4.3,6.8 L7.4,3.4" fill="none" stroke="#fff" stroke-width="1.4"/></svg>Carpet cleaning</li>
        <li><svg viewBox="0 0 10 10"><circle cx="5" cy="5" r="5" fill="var(--green)"/><path d="M2.6,5.2 L4.3,6.8 L7.4,3.4" fill="none" stroke="#fff" stroke-width="1.4"/></svg>Deodorizing and<br>sanitizing</li>
      </ul>
      <div class="card-photo card-photo--home" role="img" aria-label="Photo of a person vacuuming a bright living room floor"></div>
    </section>

    <p class="call-pill">Call us to find out how you can save money this month!</p>

    <p class="phone-line">
      <svg viewBox="0 0 24 24" aria-hidden="true"><path fill="var(--ink)" d="M6.6 10.8a15.1 15.1 0 0 0 6.6 6.6l2.2-2.2c.3-.3.7-.4 1-.2 1.1.4 2.3.6 3.6.6.6 0 1 .4 1 1V20c0 .6-.4 1-1 1A17 17 0 0 1 3 4c0-.6.4-1 1-1h3.5c.6 0 1 .4 1 1 0 1.3.2 2.5.6 3.6.1.3 0 .7-.2 1z"/></svg>
      <span>(555) 014 27 83</span>
    </p>
  </main>
</body>
</html>
```